Locksmith Business Cards

My father-in-law is in need of new business cards for his locksmith business and I need to impress him. Kindly help me out!

You can see the previous business card attached. It is a family run business in North Wales.

No individual names on the cards.

Key Things to Feature:
- The words "Prompt", "Local", "Reliable" (as you can see under the logo on the website)
- 24h Emergency Service
- Covering All of North Wales, the Wirral and Chester
- The color blue
- A key or a lock would be interesting (similar to the ones that come up when you google locksmith business card)

Optional (only if design includes bullet points, like the example below):
https://imgvaultcdn.net/samples/208314/55172/55172_3904821_208314_image.jpg
- Residential / Commercial / Automotive
- Alarms & Cameras
- Key Cutting & Safes

https://www.brynhafod-locksmiths.co.uk/

Industry/Entity Type

Locksmith

Contact Information for Business Card

01632 960 418
07700 900 362
brynhafodlocksmiths@mailvane.com
Brynhafod Locksmiths, The Willow Barn, 7 Tannery Rd., Llandudno LL99 4QX
www.brynhafod-locksmiths.co.uk

Requirements
Must have
• - The words "Prompt", "Local", "Reliable" (as you can see under the logo on the website)
• - 24h Emergency Service
• - Covering All of North Wales, the Wirral and Chester
Nice to have
• - A key or a lock would be interesting (similar to the ones that come up when you google locksmith business card)

```html
<!DOCTYPE html>
<html lang="en">
<head>
<meta charset="utf-8">
<title>Brynhafod Locksmiths – Business Cards</title>
<link rel="stylesheet" href="https://fonts.googleapis.com/css2?family=Oswald:wght@500&family=Roboto:wght@400&display=swap">
<style>
  :root {
    --page-bg: #3a3a3d;
    --navy: #1c1f55;
    --indigo: #3a4392;
    --periwinkle: #6b7dc2;
    --charcoal: #2a2a2d;
    --white: #ffffff;
    --logo-blue: #3f4a9c;
  }
  * { box-sizing: border-box; margin: 0; padding: 0; }
  html, body {
    width: 1200px; height: 900px; overflow: hidden;
    background: var(--page-bg);
    font-family: "Roboto", Arial, sans-serif;
    color: var(--white);
  }
  .sheet {
    width: 1200px; height: 900px;
    display: flex; flex-direction: column; align-items: center; justify-content: center; gap: 40px;
  }
  .card {
    position: relative; width: 660px; height: 400px; overflow: hidden;
    box-shadow: 0 10px 24px rgba(0,0,0,.45);
  }

  /* Front */
  .card--front {
    background: linear-gradient(110deg, var(--navy) 0%, var(--indigo) 50%, var(--periwinkle) 100%);
    display: flex; flex-direction: column; align-items: center; justify-content: center;
    text-align: center;
  }
  .wordmark {
    font-family: "Oswald", "Arial Narrow", sans-serif; font-weight: 500;
    text-transform: uppercase; line-height: .95; letter-spacing: .5px;
  }
  .card--front .wordmark { font-size: 46px; color: var(--white); margin-bottom: 14px; }
  .tagline { font-size: 15px; line-height: 1.3; letter-spacing: .3px; }
  .tagline--values { letter-spacing: 1px; }

  /* Back */
  .card--back { background: var(--charcoal); }
  .card__wave { position: absolute; inset: 0; }
  .card--back .wordmark {
    position: absolute; left: 40px; top: 36px;
    font-size: 44px; color: var(--logo-blue);
  }
  .address {
    position: absolute; right: 36px; top: 200px;
    text-align: right; font-size: 19px; line-height: 1.45;
  }
  .services {
    position: absolute; left: 40px; top: 236px; list-style: none;
    font-size: 19px; line-height: 1.4;
  }
  .services li { display: flex; align-items: center; gap: 8px; }
  .services svg { width: 30px; height: 14px; flex: none; }
  .contacts {
    position: absolute; right: 26px; bottom: 20px; list-style: none;
    font-size: 19px; line-height: 1.45; text-align: right;
  }
  .contacts li { display: flex; align-items: center; justify-content: flex-end; gap: 10px; }
  .contacts a { color: inherit; text-decoration: none; }
  .contacts svg { width: 20px; height: 20px; flex: none; }
</style>
</head>
<body>
<main class="sheet">

  <section class="card card--front">
    <h1 class="wordmark">Brynhafod<br>Locksmiths</h1>
    <p class="tagline tagline--values">PROMPT - LOCAL - RELIABLE</p>
    <p class="tagline">24h Emergency Service</p>
    <p class="tagline">Covering All of North Wales, the Wirral and Chester</p>
  </section>

  <section class="card card--back">
    <svg class="card__wave" viewBox="0 0 660 400" aria-hidden="true">
      <defs>
        <linearGradient id="waveFill" x1="0" y1="0" x2="1" y2="0">
          <stop offset="0" stop-color="#1c1f55"/>
          <stop offset=".55" stop-color="#4a58a8"/>
          <stop offset="1" stop-color="#6b7dc2"/>
        </linearGradient>
      </defs>
      <path d="M0,192 C180,170 300,255 420,290 C520,318 600,312 660,306 L660,400 L0,400 Z" fill="url(#waveFill)"/>
      <path d="M300,232 C390,280 490,305 660,298 L660,312 C500,320 390,295 300,232 Z" fill="#4f5fb0"/>
    </svg>

    <h2 class="wordmark">Brynhafod<br>Locksmiths</h2>

    <address class="address">
      The Willow Barn, 7 Tannery Rd.<br>
      Llandudno LL99 4QX
    </address>

    <ul class="services">
      <li><svg viewBox="0 0 30 14"><circle cx="6" cy="7" r="4.5" fill="none" stroke="#fff" stroke-width="1.6"/><path d="M10.5 7H28M22 7v4M26 7v3" stroke="#fff" stroke-width="1.6" fill="none"/></svg>Residential</li>
      <li><svg viewBox="0 0 30 14"><circle cx="6" cy="7" r="4.5" fill="none" stroke="#fff" stroke-width="1.6"/><path d="M10.5 7H28M22 7v4M26 7v3" stroke="#fff" stroke-width="1.6" fill="none"/></svg>Commercial</li>
      <li><svg viewBox="0 0 30 14"><circle cx="6" cy="7" r="4.5" fill="none" stroke="#fff" stroke-width="1.6"/><path d="M10.5 7H28M22 7v4M26 7v3" stroke="#fff" stroke-width="1.6" fill="none"/></svg>Automotive</li>
      <li><svg viewBox="0 0 30 14"><circle cx="6" cy="7" r="4.5" fill="none" stroke="#fff" stroke-width="1.6"/><path d="M10.5 7H28M22 7v4M26 7v3" stroke="#fff" stroke-width="1.6" fill="none"/></svg>Alarms &amp; Cameras</li>
      <li><svg viewBox="0 0 30 14"><circle cx="6" cy="7" r="4.5" fill="none" stroke="#fff" stroke-width="1.6"/><path d="M10.5 7H28M22 7v4M26 7v3" stroke="#fff" stroke-width="1.6" fill="none"/></svg>Key Cutting &amp; Safes</li>
    </ul>

    <ul class="contacts">
      <li>01632 960 418<svg viewBox="0 0 20 20"><path d="M3 8c0-3 3-4 7-4s7 1 7 4l-3 1-1-2H7L6 9 3 8zM5 10h10l1 7H4z" fill="#fff"/></svg></li>
      <li>07700 900 362<svg viewBox="0 0 20 20"><path d="M3 8c0-3 3-4 7-4s7 1 7 4l-3 1-1-2H7L6 9 3 8zM5 10h10l1 7H4z" fill="#fff"/></svg></li>
      <li>brynhafodlocksmiths@mailvane.com<svg viewBox="0 0 20 20"><rect x="2" y="5" width="16" height="11" rx="1" fill="#fff"/><path d="M2.5 5.5 10 11l7.5-5.5" stroke="#4a58a8" stroke-width="1.4" fill="none"/></svg></li>
      <li><a href="https://www.brynhafod-locksmiths.co.uk/">www.brynhafod-locksmiths.co.uk</a><svg viewBox="0 0 20 20"><circle cx="10" cy="10" r="7.5" fill="none" stroke="#fff" stroke-width="1.6"/><ellipse cx="10" cy="10" rx="3.2" ry="7.5" fill="none" stroke="#fff" stroke-width="1.2"/><path d="M2.5 10h15" stroke="#fff" stroke-width="1.2"/></svg></li>
    </ul>
  </section>

</main>
</body>
</html>
```